Custom Cabinet Shop Needs a website design

Hi,
We need a website for a Custom Cabinet Shop and Cabinet parts manufacturing business.
The business has two sides to it. One side provides custom Kitchens, vanities, entertainment units, offices and what not to homeowners and contractors.
The 2nd side of the business provides built to order cabinet boxes and other parts required to put together a project to other cabinet shops, small contractors looking to install there own cabinets.
Website will need a Gallery to display work.
Color scheme to go well with logo.
current website is www.brambleoakcustomcabinets.com
being changed to www.brambleoak.ca
Logo Included in attached files.
Tagline "Joinery with Spirit"
Mission Statement "Our passion is to deliver inspired cabinetry solutions to suit all your needs, supported by our phenomenal star class customer service"
The website should convey quality and professionalism.
Thank you.
Homeowners/ Contractors
Entertainment

```html
<!DOCTYPE html>
<html lang="en">
<head>
<meta charset="utf-8">
<title>Brambleoak Custom Cabinets</title>
<link href="https://fonts.googleapis.com/css2?family=Oswald:wght@400;500;700&family=Open+Sans:wght@400;600;700&display=swap" rel="stylesheet">
<style>
:root{
  --black:#0d0d0d;
  --dark:#1a1a1a;
  --orange:#e8461d;
  --white:#ffffff;
  --text:#555555;
  --light:#eeeeee;
  --line:#d9d9d9;
}
*{margin:0;padding:0;box-sizing:border-box}
html,body{width:857px;height:1200px;overflow:hidden;background:var(--white);font-family:"Open Sans",Arial,sans-serif}
.page{position:relative;width:857px;height:1200px}

.site-header{position:absolute;top:0;left:0;width:857px;height:95px;background:var(--black)}
.brand{position:absolute;left:70px;top:28px;display:flex;align-items:center;gap:10px}
.brand-dot{width:34px;height:34px;border-radius:50%;background:var(--orange)}
.brand-name{font-family:"Oswald",sans-serif;font-weight:700;font-size:26px;color:var(--white);letter-spacing:1px}
.main-nav{position:absolute;right:62px;top:38px;display:flex;align-items:center;gap:6px}
.main-nav a{font-family:"Oswald",sans-serif;font-size:11px;color:var(--white);text-decoration:none;padding:5px 11px;letter-spacing:.5px}
.main-nav a.active{background:var(--orange)}
.search-icon{margin-left:8px}

.hero{position:absolute;top:95px;left:0;width:857px;height:360px;background:linear-gradient(160deg,#2a221c 0%,#5a4533 40%,#3a2c22 65%,#1c1713 100%)}
.hero-title{position:absolute;top:200px;width:100%;text-align:center;font-family:"Oswald",sans-serif;font-weight:700;font-size:28px;color:var(--white);letter-spacing:1px;text-transform:uppercase}
.hero-arrow{position:absolute;top:256px;width:26px;height:26px;border-radius:50%;background:rgba(255,255,255,.85);display:flex;align-items:center;justify-content:center}
.hero-arrow.prev{left:8px}.hero-arrow.next{right:8px}

.welcome{position:absolute;top:470px;left:0;width:857px;text-align:center}
.section-title{font-family:"Oswald",sans-serif;font-weight:500;font-size:22px;color:#222;text-transform:uppercase}
.mission{margin:10px auto 0;width:620px;font-size:10px;color:var(--orange)}
.intro{margin:6px auto 0;width:620px;font-size:9px;line-height:14px;color:var(--text)}
.btn{display:inline-block;margin-top:22px;background:var(--orange);color:var(--white);font-family:"Oswald",sans-serif;font-size:10px;padding:8px 18px;letter-spacing:.5px}

.works{position:absolute;top:650px;left:0;width:857px;text-align:center}
.works-grid{position:absolute;top:42px;left:75px;width:716px;display:grid;grid-template-columns:repeat(3,225px);column-gap:20px;row-gap:24px}
.work-card{position:relative;height:126px;border:1px solid var(--line)}
.work-photo{position:absolute;inset:0}
.work-label{position:absolute;left:0;bottom:0;width:100%;height:20px;background:var(--white);font-family:"Oswald",sans-serif;font-size:9px;font-weight:500;color:#222;text-align:left;padding:4px 8px;text-transform:uppercase}

.newsletter{position:absolute;top:982px;left:0;width:857px;height:98px;background:var(--light)}
.newsletter .mail-icon{position:absolute;left:150px;top:30px}
.field{position:absolute;top:36px;height:26px;background:var(--white);border:1px solid var(--line);font-size:8px;color:#999;padding:7px 10px}
.field.name{left:250px;width:180px}
.field.email{left:440px;width:180px}
.subscribe{position:absolute;left:630px;top:36px;width:85px;height:26px;background:var(--orange);color:var(--white);font-family:"Oswald",sans-serif;font-size:10px;text-align:center;line-height:26px}

.site-footer{position:absolute;top:1080px;left:0;width:857px;height:120px;background:var(--dark);text-align:center}
.social{margin-top:22px;display:flex;justify-content:center;gap:8px}
.social span{width:20px;height:20px;border-radius:50%;border:1px solid #777}
.footer-links{margin-top:16px;font-size:8px;color:#bbb}
.footer-links span{margin:0 6px}
.copyright{margin-top:6px;font-size:7px;color:#888}
</style>
</head>
<body>
<div class="page">
  <header class="site-header">
    <div class="brand"><span class="brand-dot"></span><span class="brand-name">BRAMBLEOAK</span></div>
    <nav class="main-nav">
      <a class="active">HOME</a><a>GALLERY</a><a>SERVICES</a><a>WARRANTY</a><a>CONTACT</a>
      <svg class="search-icon" width="12" height="12" viewBox="0 0 12 12"><circle cx="5" cy="5" r="3.8" fill="none" stroke="#fff" stroke-width="1.5"/><line x1="8" y1="8" x2="11" y2="11" stroke="#fff" stroke-width="1.5"/></svg>
    </nav>
  </header>

  <section class="hero" role="img" aria-label="Photo of a finished basement bar with dark cabinetry, stools and pendant lights">
    <h1 class="hero-title">Joinery with Spirit</h1>
    <div class="hero-arrow prev"><svg width="10" height="10" viewBox="0 0 10 10"><path d="M6.5 1.5 3 5l3.5 3.5" fill="none" stroke="#333" stroke-width="1.6"/></svg></div>
    <div class="hero-arrow next"><svg width="10" height="10" viewBox="0 0 10 10"><path d="M3.5 1.5 7 5 3.5 8.5" fill="none" stroke="#333" stroke-width="1.6"/></svg></div>
  </section>

  <section class="welcome">
    <h2 class="section-title">Welcome to Brambleoak</h2>
    <p class="mission">Our passion is to deliver inspired cabinetry solutions to suit all your needs, supported by our phenomenal star class customer service</p>
    <p class="intro">From the first sketch to the final hinge, our shop builds kitchens, vanities, entertainment units and offices for homeowners and contractors, and supplies built-to-order cabinet boxes and parts to fellow shops and installers across the region.</p>
    <span class="btn">VIEW MORE INFO</span>
  </section>

  <section class="works">
    <h2 class="section-title">Our Works</h2>
    <div class="works-grid">
      <div class="work-card"><div class="work-photo" role="img" aria-label="Living room with fireplace built-ins" style="background:linear-gradient(135deg,#6b5a4a,#2e2620)"></div><div class="work-label">Fireside Built-Ins</div></div>
      <div class="work-card"><div class="work-photo" role="img" aria-label="Modern kitchen with red-brown cabinets" style="background:linear-gradient(135deg,#8a3e28,#c9b8a6)"></div><div class="work-label">Modern Kitchen Island</div></div>
      <div class="work-card"><div class="work-photo" role="img" aria-label="Dark walnut bar counter" style="background:linear-gradient(135deg,#3b2a1e,#a07a4e)"></div><div class="work-label">Walnut Bar Counter</div></div>
      <div class="work-card"><div class="work-photo" role="img" aria-label="Bright open kitchen with light cabinets" style="background:linear-gradient(135deg,#d8d2c8,#8c7f70)"></div><div class="work-label">Bright Open Kitchen</div></div>
      <div class="work-card"><div class="work-photo" role="img" aria-label="Bathroom vanity with dark wood" style="background:linear-gradient(135deg,#4a3a30,#bfb4a8)"></div><div class="work-label">Bathroom Vanity Suite</div></div>
      <div class="work-card"><div class="work-photo" role="img" aria-label="Dining room with cabinetry" style="background:linear-gradient(135deg,#9a8a78,#e2dcd4)"></div><div class="work-label">Dining Room Cabinets</div></div>
    </div>
  </section>

  <section class="newsletter">
    <svg class="mail-icon" width="40" height="36" viewBox="0 0 40 36"><path d="M3 14 20 2l17 12v20H3z" fill="none" stroke="#e8461d" stroke-width="2"/><path d="M3 14l17 12 17-12" fill="none" stroke="#e8461d" stroke-width="2"/></svg>
    <div class="field name">Enter your name</div>
    <div class="field email">Enter your email address</div>
    <div class="subscribe">SUBSCRIBE</div>
  </section>

  <footer class="site-footer">
    <div class="social"><span></span><span></span><span></span><span></span><span></span></div>
    <div class="footer-links"><span>Privacy Policy</span>|<span>Client Login</span>|<span>Warranty Form</span>|<span>Terms &amp; Conditions</span></div>
    <div class="copyright">Copyright © Brambleoak Custom Cabinets 2015. All rights reserved.</div>
  </footer>
</div>
</body>
</html>
```